The 22 Rules and Traps of House Lending or the 22 things that will derail your transaction and how to prevent them.

I am looking to do a series of 4 to 5 e-books that should have a consistent format and theme

The first of these should be entitled, "The 22 Rules and Traps of House Lending" That is similar in style to the attached e-book.
The attached e-book is pretty much the style that I am looking for, The same format can be followed. I have attached a black and white head shot image for the head shot areas that appears on page two of the attached e-book. I have also attached my company logo.
Please feel free to use the same or similar colors in my logo for the lay-out of the e-book. However please do not feel limited to those colors. - Feel free to use your imagination.

The content can be found here.

http://www.fredtheloanfox.example/loan-advice.php

For the final “About” page of the e-book - Please entitle it… About Fred the Loan Fox.
The content for the last page can be found in the attached document - Owen Thistlewood bio2

The first page is where the creativity come in

Requirements
Must have
• Note that this project is for one e-book - However, once the designer and format is chosen the remainder of the projects will be launched

```html
<!DOCTYPE html>
<html lang="en">
<head>
<meta charset="utf-8">
<title>The 22 Rules and Traps of House Lending – Spreads</title>
<link href="https://fonts.googleapis.com/css2?family=Jost:wght@400;500;700&family=Crimson+Pro:ital,wght@0,600;0,700;1,700;1,800&display=swap" rel="stylesheet">
<style>
  :root {
    --backdrop: #f6eea6;
    --sky: #00aeef;
    --navy: #263862;
    --ink: #2b3550;
    --red: #ee1c25;
    --grey: #7d8088;
    --white: #ffffff;
  }
  * { margin: 0; padding: 0; box-sizing: border-box; }
  html, body { width: 1200px; height: 1020px; overflow: hidden; }
  body { background: var(--backdrop); font-family: "Jost", sans-serif; color: var(--ink); position: relative; }

  .page { position: absolute; width: 345px; height: 460px; background: var(--white); overflow: hidden; }
  .col-1 { left: 53px; } .col-2 { left: 432px; } .col-3 { left: 810px; }
  .row-1 { top: 35px; } .row-2 { top: 520px; }

  .brand { font-family: "Crimson Pro", serif; font-weight: 700; color: var(--navy); letter-spacing: .02em; }

  /* Cover */
  .cover { background: var(--sky); text-align: center; }
  .cover .brand-badge { position: absolute; top: 22px; left: 50%; transform: translateX(-50%); background: var(--white); padding: 3px 7px; font-size: 10px; }
  .cover-title { position: absolute; top: 66px; left: 0; right: 0; font-family: "Crimson Pro", serif; font-style: italic; font-weight: 800; color: var(--navy); line-height: 1.05; }
  .cover-title .line-1 { font-size: 20px; }
  .cover-title .num { font-size: 38px; color: var(--white); }
  .cover-title .small { font-size: 12px; }
  .cover-title .line-2 { font-size: 29px; display: block; margin-top: 2px; }
  .cover-art { position: absolute; left: 77px; top: 149px; width: 170px; height: 170px; border-radius: 50%; background: radial-gradient(circle at 50% 45%, #ffffff 0 60%, #e3f6fd 100%); }
  .cover-author { position: absolute; bottom: 34px; left: 0; right: 0; color: var(--white); font-size: 8.5px; }
  .cover-author b { font-weight: 700; }

  .blank { background: var(--navy); }

  /* Intro */
  .portrait { position: absolute; left: 28px; top: 25px; width: 74px; height: 74px; border-radius: 50%; background: linear-gradient(160deg, #b9b9b9, #3a3a3a); border: 3px solid var(--sky); }
  .intro-head { position: absolute; left: 25px; top: 105px; font-family: "Crimson Pro", serif; font-weight: 700; font-variant: small-caps; line-height: .95; }
  .intro-head .a { color: var(--sky); font-size: 34px; }
  .intro-head .b { color: var(--red); font-size: 34px; }
  .intro-head .sm { color: var(--navy); font-size: 14px; }
  .intro-head .sub { display: block; font-size: 13px; color: var(--grey); margin-top: 4px; }
  .intro-head .sub .sm { font-size: 11px; }
  .intro-copy { position: absolute; left: 25px; right: 48px; top: 190px; font-size: 6.3px; line-height: 1.35; }

  /* Rule pages */
  .rules { padding: 34px 24px 0; }
  .rule { margin-bottom: 22px; }
  .rule h2 { font-weight: 500; font-size: 11.3px; line-height: 1.25; color: var(--navy); margin-bottom: 7px; }
  .rule h2 .dont { color: var(--red); font-weight: 700; }
  .rule h2 .do { color: var(--sky); font-weight: 700; }
  .rule p { font-size: 5.6px; line-height: 1.35; margin-bottom: 6px; }
  .rule p.note { font-weight: 700; color: var(--grey); font-size: 6.6px; line-height: 1.4; }

  .folio { position: absolute; left: 24px; right: 24px; bottom: 25px; display: flex; align-items: center; gap: 5px; font-family: "Crimson Pro", serif; font-size: 5.6px; color: var(--grey); font-variant: small-caps; }
  .folio .brand { font-size: 8.5px; padding-right: 5px; border-right: 1px solid var(--grey); }
  .folio .title b { color: var(--navy); }
  .folio .num { margin-left: auto; width: 10px; height: 10px; background: var(--navy); color: var(--white); font-family: "Jost", sans-serif; font-size: 6px; display: flex; align-items: center; justify-content: center; font-variant: normal; }

  /* About */
  .about { background: var(--sky); color: var(--navy); padding: 38px 24px 0; }
  .about h1 { font-family: "Crimson Pro", serif; font-variant: small-caps; font-weight: 700; font-size: 15px; margin-bottom: 14px; }
  .about h1 .name { color: var(--white); font-size: 30px; }
  .about p { font-size: 5.7px; line-height: 1.45; margin-bottom: 8px; }
  .about blockquote { font-weight: 700; font-style: italic; color: var(--white); font-size: 9px; line-height: 1.15; margin-bottom: 9px; }
  .about blockquote span { font-weight: 400; font-style: normal; color: var(--navy); font-size: 7px; }
  .about p.cta { font-weight: 700; font-size: 6.2px; }
  .about .folio { color: var(--white); }
  .about .folio .brand { color: var(--white); border-color: var(--white); }
  .about .folio .title b { color: var(--navy); }
  .about .folio .num { background: var(--white); color: var(--navy); }
</style>
</head>
<body>

<section class="page cover col-1 row-1">
  <div class="brand brand-badge">Harbor Crest</div>
  <h1 class="cover-title"><span class="line-1">The <span class="num">22</span> Rules <span class="small">and</span> Traps</span><span class="line-2">of House Lending</span></h1>
  <div class="cover-art" role="img" aria-label="Illustration of a lender and buyer at a desk weighing a checklist, with clock, coins and house icons"></div>
  <p class="cover-author"><b>Fred</b> the Loan Fox</p>
</section>

<section class="page blank col-2 row-1"></section>

<section class="page col-3 row-1">
  <div class="portrait" role="img" aria-label="Black and white head shot of Fred the Loan Fox"></div>
  <h1 class="intro-head"><span class="a">Rules</span> <span class="sm">and</span><br><span class="b">Traps</span><span class="sub"><span class="sm">of</span> House Lending</span></h1>
  <p class="intro-copy">To help my clients have as stress-free experience as possible when buying or refinancing their home, I have compiled this list of rules and traps to help them keep from making common oversights and errors which can potentially delay their closings.</p>
  <footer class="folio"><span class="brand">Harbor Crest</span><span class="title">The 22 <b>Rules</b> and <b>Traps</b> of House Lending</span><span class="num">3</span></footer>
</section>

<section class="page rules col-1 row-2">
  <article class="rule">
    <h2><span class="dont">Don’t</span> apply for two mortgage at<br>the same time for the same transaction.</h2>
    <p>Popular wisdom states that it is always best to “shop around” for the best terms for your mortgage. While this is true, once you have decided upon an acceptable lender with acceptable terms, this is where your shopping should end. If you have two mortgage brokers working on your loan simultaneously it can adversely effect your credit and the underwriting process. If a particular lender learns that you are trying to obtain financing for a transaction they are working on you run the risk of the lender canceling your loan application.</p>
  </article>
  <article class="rule">
    <h2><span class="do">Do</span> let your agent or mortgage professional know if you are planning to travel while applying for a loan.</h2>
    <p>Going out of town during the process of securing home financing can create havoc with the closing of your loan. If you are planning to be out of town let both your real estate agent and mortgage professional know early enough so they can plan accordingly. Planning the closing of your loan transaction around your trip can be easily done if your agent and mortgage professional are aware of your travel plans.</p>
    <p>A good rule of thumb is to let them know three weeks in advance. Emergency trips do happen, and if you need to be out of town on an emergency basis please let your agent and mortgage professional know as soon as possible so appropriate planning can take place.</p>
    <p>Please also provide a way that you can be contacted so if you are required to provide paperwork, or if paperwork needs to be sent to you, it can easily be done while you are out of town.</p>
  </article>
  <article class="rule">
    <h2><span class="do">Do</span> continue making your payments on your mortgages or other loans during the underwriting process.</h2>
    <p>This one may seem quite obvious but, some borrowers wrongly assume that if they are selling a home, refinancing a home mortgage, or paying off debt with a debt consolidation mortgage, those loans will soon be eliminated so the necessity to keep those payments going is also eliminated. Not keeping up on all of your payment could result in a late-payment penalty on your existing mortgage and/or a 30-day late on your credit.</p>
    <p>It is very important to keep up on all payments during the loan process to keep any negative information from being reported to the credit agencies and potentially damaging your credit score.</p>
  </article>
  <footer class="folio"><span class="brand">Harbor Crest</span><span class="title">The 22 <b>Rules</b> and <b>Traps</b> of House Lending</span><span class="num">4</span></footer>
</section>

<section class="page rules col-2 row-2">
  <article class="rule">
    <h2><span class="dont">Don’t</span> apply for any new credit during the underwriting process.</h2>
    <p>Some borrowers can get caught up in a buying fervor when purchasing a house. They want to furnish their new home and get appliances for their new kitchen. Some are temped to apply for new credit. Every time someone applies for credit, the new creditor will obtain a copy of your credit report to establish creditworthiness.</p>
    <p class="note">These inquires can adversely effect a borrower’s credit score, which in turn may adversely effect the underwriting of your loan, and possibly the final rate of your mortgage.</p>
  </article>
  <article class="rule">
    <h2><span class="dont">Don’t</span> get multiple inquiries during the underwriting process.</h2>
    <p>Similar to the Don’t mentioned above is to avoid having multiple mortgage companies obtain multiple copies of your credit while researching the best mortgage company to do your loan for you. While I generally encourage shopping for the best rate and fee structure for your purchase or refinance, it is generally a bad idea to allow multiple mortgage companies to obtain copies of your credit as this can adversely effect your credit score.</p>
    <p class="note">When in doubt it is always best to ask the advise of your mortgage professional.</p>
  </article>
  <article class="rule">
    <h2><span class="dont">Don’t</span> incur any new debt during the underwriting process.</h2>
    <p>This don’t is a continuation of the last one. When you apply for and obtain new credit you create a underwriting double-whammy. Not only have you incurred an unnecessary credit inquiry on your credit report, you have increased your debt load, which can adversely affect your debt-to-income ratio.</p>
    <p class="note">If your loan is at the edge of the lender’s allowable debt-to-income ratio and you apply for and obtain new credit, that new debt may be just enough to result in a loan denial. The best rule of thumb is to resist the urge to buy new furniture or appliances until after your mortgage transaction has closed.</p>
  </article>
  <footer class="folio"><span class="brand">Harbor Crest</span><span class="title">The 22 <b>Rules</b> and <b>Traps</b> of House Lending</span><span class="num">5</span></footer>
</section>

<section class="page about col-3 row-2">
  <h1>About <span class="name">Fred</span> the Loan Fox</h1>
  <p>Here’s all what you need to know about the mortgage industry today: One large lender is promoting a tool that doesn’t require you to interact with a human to make one of the biggest financial decisions of your life.</p>
  <p>I believe you deserve better. And I’ve spent nearly 20 years providing my clients with the guidance they need so they don’t just get a loan — they get the right loan.</p>
  <p>You see, the mortgage process isn’t quite as simple as the ads make it seem. It takes knowledge and experience to navigate, particularly in a competitive real-estate market, where the right combination of speed and expertise can make the difference between a successful offer and losing out on your dream home.</p>
  <p>My clients, many of whom are first-time homebuyers or have run into resistance from other lenders, always know where they stand in that complex process. That’s because I take the time to explain their options, so they can make an informed, confident decision. And most of them, like the clients below, would even say that I’m an advisor and advocate first, and a mortgage professional second.</p>
  <blockquote>“I felt that Fred really cared for me, rather than seeing the whole process as just another transaction.” <span>Porchview comment</span></blockquote>
  <blockquote>“Fred did a fantastic job of seeing me through the entire process, from ‘newbie’ to homeowner.” <span>Porchview comment</span></blockquote>
  <p>I’m still in contact continue to be a resource with a number for many of those my past clients, often years after they purchased or refinanced their homes. They come to me because they know I provide a level of personal service uncommon in this industry. They come to me because they know I care. And they come to me because they know I have the willingness, and the knowledge, to help.</p>
  <p class="cta">I’d love to help you — whether you’re buying, refinancing or just weighing your options. Email me or give me a call today.</p>
  <footer class="folio"><span class="brand">Harbor Crest</span><span class="title">The 22 <b>Rules</b> and <b>Traps</b> of House Lending</span><span class="num">7</span></footer>
</section>

</body>
</html>
```